Lanternfield Drinks business cards

We need a business card design for our new logo. The company is modern, progressive, professional, yet approachable. The key products are ready to drink bottles and cans of coffee based beverages.
These cards will be a critical part of the first impression made by our sales organization, business development team, and all external facing personnel.
Card can be a vertical or horizontal orientation.

Target Market(s)

Customers, suppliers, business partners

Industry/Entity Type

Business

Contact Information for Business Card

Business cards should feature Company Name and Logo.

Font styles to use
Serif

Colors

Designer to choose colors to be used in the design.

Requirements
Must have
• Strong readability of Name, phone #, mobile number and email address.
• Job title, website url, Street Address, and other details can be secondary level readability.
Nice to have
• High impact, simplistic quality design.
• Ok to utilize the 'H in the box' separate from the company name

```html
<!DOCTYPE html>
<html lang="en">
<head>
<meta charset="utf-8">
<title>Lanternfield Drinks — Business Cards</title>
<link href="https://fonts.googleapis.com/css2?family=Crimson+Text:ital,wght@0,400;0,600;0,700;1,400&display=swap" rel="stylesheet">
<style>
  :root{
    --backdrop:#c9c9c9;
    --orange-top:#df8535;
    --orange-bottom:#bf4d2a;
    --brand-red:#c9472a;
    --brand-amber:#d98a2e;
    --card-white:#f4f4f3;
    --ink:#2b2522;
    --ink-soft:#3d3532;
    --on-orange:#f6efe9;
  }
  *{box-sizing:border-box;margin:0;padding:0}
  html,body{width:1200px;height:576px;overflow:hidden}
  body{background:var(--backdrop);position:relative;font-family:"Crimson Text",Georgia,serif;color:var(--ink)}

  .card{position:absolute;border-radius:13px;overflow:hidden;box-shadow:0 3px 8px rgba(0,0,0,.22)}

  /* Front */
  .card--front{left:82px;top:139px;width:484px;height:293px;
    background:linear-gradient(180deg,var(--orange-top) 0%,var(--orange-bottom) 100%)}
  .front-brand{position:absolute;left:0;right:0;top:78px;text-align:center}
  .front-brand__square{display:block;margin:0 auto 12px;width:76px;height:76px;border:3px solid var(--on-orange)}
  .front-brand__name{font-weight:700;font-size:36px;letter-spacing:1px;text-transform:uppercase;color:var(--on-orange);line-height:1.05}

  /* Back */
  .card--back{left:602px;top:138px;width:481px;height:292px;background:var(--card-white)}
  .back-brand{position:absolute;left:28px;top:30px;display:flex;align-items:center;gap:14px}
  .back-brand__square{width:68px;height:68px;border:3px solid var(--brand-red);flex:none}
  .back-brand__name{font-weight:700;font-size:30px;letter-spacing:.5px;text-transform:uppercase;color:var(--brand-red);line-height:1}

  .person{position:absolute;left:28px;top:141px;right:28px}
  .person__name{font-weight:600;font-size:20px;color:var(--brand-red);line-height:1.1}
  .person__title{display:flex;align-items:center;gap:8px;font-style:italic;font-size:11.5px;color:var(--ink-soft);margin-top:2px}
  .person__rule{flex:1;height:1px;background:var(--brand-amber)}

  .contacts{position:absolute;left:32px;top:196px;list-style:none}
  .contacts li{display:flex;align-items:center;gap:9px;font-size:13px;line-height:16.7px;color:var(--ink)}
  .contacts svg{width:10px;height:10px;fill:var(--brand-red);flex:none}

  .address{position:absolute;right:27px;top:229px;text-align:right;font-size:13px;line-height:16.7px;color:var(--ink)}

  .back-band{position:absolute;left:0;bottom:0;width:100%;height:10px}
</style>
</head>
<body>

<section class="card card--front" aria-label="Card front">
  <div class="front-brand">
    <span class="front-brand__square"></span>
    <p class="front-brand__name">Lanternfield<br>Drinks</p>
  </div>
</section>

<section class="card card--back" aria-label="Card back">
  <div class="back-brand">
    <span class="back-brand__square"></span>
    <p class="back-brand__name">Lanternfield<br>Drinks</p>
  </div>

  <div class="person">
    <p class="person__name">Maren Ellery Shaw</p>
    <p class="person__title">Managing Director <span class="person__rule"></span></p>
  </div>

  <ul class="contacts">
    <li>
      <svg viewBox="0 0 10 10" aria-hidden="true"><path d="M1 3.2C1 2 2.5 1.4 5 1.4S9 2 9 3.2V4H7V3.2H3V4H1z"/><path d="M2.3 4.6h5.4L8.6 8.6H1.4z"/></svg>
      555.014.2298
    </li>
    <li>
      <svg viewBox="0 0 10 10" aria-hidden="true"><path d="M2.5 0.5h5a1 1 0 0 1 1 1v7a1 1 0 0 1-1 1h-5a1 1 0 0 1-1-1v-7a1 1 0 0 1 1-1zM2.7 1.8v5.4h4.6V1.8z"/></svg>
      555.014.7731
    </li>
    <li>
      <svg viewBox="0 0 10 10" aria-hidden="true"><path d="M0.5 2h9v6h-9z"/><path d="M1.2 2.6L5 5.6 8.8 2.6" fill="none" stroke="#f4f4f3" stroke-width=".8"/></svg>
      maren@lanternfielddrinks.com
    </li>
    <li>
      <svg viewBox="0 0 10 10" aria-hidden="true"><circle cx="5" cy="5" r="4.3"/><path d="M0.8 5h8.4M5 0.8v8.4M5 0.8C3 3 3 7 5 9.2M5 0.8C7 3 7 7 5 9.2" fill="none" stroke="#f4f4f3" stroke-width=".7"/></svg>
      www.lanternfielddrinks.com
    </li>
  </ul>

  <p class="address">78 Harrow Lane,<br>Brookvale, US 40213</p>

  <svg class="back-band" viewBox="0 0 481 10" preserveAspectRatio="none" aria-hidden="true">
    <rect x="0" y="0" width="481" height="10" fill="var(--brand-red)"/>
    <polygon points="350,10 395,0 481,0 481,10" fill="var(--brand-amber)"/>
  </svg>
</section>

</body>
</html>
```